Marlowby Services Website Design

We have most content but require a professional design. We have a logo already and will need it utilized along with several of the photos from the attached documentation.
First page should have our mission and Vision and the synapsis provided in the word document. Visitors will be prompted to select from one of our 3 divisions from this page.
Each division will have the same list of tabs : About, Services, Safety, Careers and Contact.
Photos on each divisions page should be representative of the divisions offerings. The word doc attached contains the requested content and we are open to edits that would complement and fill the website.
I like the Quorvane site www.quorvane.example - they are our competition so cant be modeled directly after this.
Please include prompts to request quote at each service page. align the format of the geotechnical page to the other 2 divisions.
I used chat gpt for some of the content so will need it optimized for SCO.

```html
<!DOCTYPE html>
<html lang="en">
<head>
<meta charset="utf-8">
<title>Marlowby Services</title>
<link rel="stylesheet" href="https://fonts.googleapis.com/css2?family=Poppins:wght@400;500;600;700&display=swap">
<style>
:root{
  --red:#ee1c25;
  --ink:#111111;
  --body:#444444;
  --pink:#fdf0f0;
  --pink-card:#fdeeee;
  --white:#ffffff;
  --footer:#0c0c0c;
}
*{margin:0;padding:0;box-sizing:border-box}
html,body{width:1200px;height:3269px;overflow:hidden}
body{position:relative;font-family:"Poppins",sans-serif;color:var(--ink);background:var(--white)}
.abs{position:absolute}
.photo{position:absolute}

/* Hero */
.hero{left:0;top:0;width:1200px;height:529px;background:linear-gradient(120deg,#3d4238 0%,#5a5c45 35%,#6d6e57 60%,#8d8e84 100%)}
.hero-shade{left:0;top:0;width:1200px;height:529px;background:linear-gradient(90deg,rgba(0,0,0,.45),rgba(0,0,0,.1))}
.logo{font-family:"Poppins",sans-serif;font-weight:700;font-size:29px;letter-spacing:3px;line-height:1}
.nav .logo{left:141px;top:20px;color:var(--white)}
.nav-links{left:647px;top:26px;display:flex;gap:26px;font-size:14px;color:var(--white)}
.btn{display:flex;align-items:center;justify-content:center;font-size:13px;font-weight:500}
.nav-cta{left:950px;top:16px;width:109px;height:36px;background:var(--red);color:var(--white)}
.hero-kicker{left:141px;top:192px;font-size:15px;color:var(--white)}
.hero-title{left:141px;top:226px;font-size:39px;font-weight:600;line-height:50px;color:var(--white);width:520px}
.hero-cta{left:141px;top:406px;width:109px;height:35px;background:var(--white);color:var(--red)}

/* Section headings */
.section-title{font-size:30px;font-weight:600;text-align:center;width:1200px;left:0}
.rule{height:2px;background:var(--red)}

/* Services */
.services-sub{left:0;width:1200px;top:678px;text-align:center;font-size:14px}
.service-card{top:741px;width:214px;height:223px;background:var(--pink-card);text-align:center}
.service-card svg{position:absolute;left:79px;top:20px}
.service-card h3{position:absolute;top:94px;left:10px;right:10px;font-size:14.5px;font-weight:600;line-height:20px}
.service-card p{position:absolute;left:16px;right:16px;font-size:11.5px;line-height:20px;color:var(--body)}

/* Vision / Mission */
.dots{display:grid;grid-template-columns:repeat(3,5px);gap:13px 10px}
.dots span{width:3px;height:3px;border-radius:50%;background:var(--red)}
.icon-badge{width:56px;height:56px;border-radius:50%;background:#fde3e3;display:flex;align-items:center;justify-content:center}
.block-title{font-size:30px;font-weight:600}
.block-text{font-size:13.5px;line-height:22.5px;color:var(--body)}

/* Divisions */
.divisions{left:0;top:1915px;width:1200px;height:552px;background:var(--pink)}
.division-card{top:2061px;width:292px;height:349px;border:1px solid #d7d7d7;background:var(--white);text-align:center}
.division-card.active{background:var(--red);border-color:var(--red);color:var(--white)}
.division-card .photo{left:7px;top:7px;width:276px;height:168px}
.division-card h3{position:absolute;top:191px;left:0;width:100%;font-size:16px;font-weight:600}
.division-card p{position:absolute;top:226px;left:14px;right:14px;font-size:11.5px;line-height:20.5px;color:var(--body)}
.division-card.active p{color:var(--white)}
.read-more{position:absolute;top:318px;left:0;width:100%;font-size:13px;font-weight:600;display:flex;justify-content:center;align-items:center;gap:6px}
.read-more span{text-decoration:underline}

/* Closing */
.closing-text{left:290px;top:2558px;width:620px;text-align:center;font-size:17px;font-weight:500;line-height:25px}
.closing-cta{left:545px;top:2800px;width:110px;height:34px;background:var(--red);color:var(--white)}

/* Footer */
.footer{left:0;top:2920px;width:1200px;height:349px;background:var(--footer);color:var(--white)}
.footer .logo{left:141px;top:76px;color:var(--red);font-size:30px}
.footer h4{font-size:16px;font-weight:500}
.footer ul{list-style:none;font-size:13px;line-height:29px}
.contact-item{display:flex;gap:10px;font-size:13px;line-height:19px}
.footer-rule{left:141px;top:290px;width:918px;height:1px;background:#3a3a3a}
.copyright{left:141px;top:310px;font-size:13px}
.socials{left:925px;top:306px;display:flex;gap:12px}
.socials span{width:24px;height:24px;border-radius:50%;background:var(--red);border:2px solid var(--white)}
</style>
</head>
<body>

<!-- Hero -->
<div class="abs photo hero" role="img" aria-label="Aerial view of a boom truck working beside a road and parked pickup trucks"></div>
<div class="abs hero-shade"></div>
<header class="nav">
  <div class="abs logo">MARLOWBY</div>
  <nav class="abs nav-links"><span>About Us</span><span>Services</span><span>Safety</span><span>Careers</span></nav>
  <div class="abs btn nav-cta">Contact Us</div>
</header>
<p class="abs hero-kicker">Delivering safe, reliable access and maintenance services to</p>
<h1 class="abs hero-title">Oil &amp; Gas, Construction, Utility &amp; Renewable energy Sector</h1>
<div class="abs btn hero-cta">Contact Us</div>

<!-- Services -->
<h2 class="abs section-title" style="top:614px">Our Services</h2>
<div class="abs rule" style="left:562px;top:659px;width:76px"></div>
<p class="abs services-sub">Delivering safe, reliable aerial access and maintenance services</p>

<div class="abs service-card" style="left:141px">
  <svg width="56" height="52" viewBox="0 0 56 52" fill="none" stroke="#ee1c25" stroke-width="2"><path d="M16 8h24l6 12H10z"/><path d="M22 8l-2 12M34 8l2 12M28 8v12"/><path d="M6 46c6-10 14-12 22-6s16 4 22-6"/><circle cx="40" cy="30" r="6"/><path d="M14 26v10M10 30h8"/></svg>
  <h3>Renewable Energy Industries</h3>
  <p style="top:147px">Lorem Ipsum is simply dummy text of the printing and typesetting industry.</p>
</div>
<div class="abs service-card" style="left:375px">
  <svg width="56" height="56" viewBox="0 0 56 56" fill="none" stroke="#ee1c25" stroke-width="2"><rect x="8" y="20" width="14" height="32"/><rect x="34" y="12" width="14" height="40"/><path d="M22 36h12M22 28h12"/><path d="M10 4h16v16"/><circle cx="28" cy="44" r="4"/><path d="M4 52h48"/></svg>
  <h3 style="top:100px">Oil &amp; Gas</h3>
  <p style="top:127px">Lorem Ipsum is simply dummy text of the printing and typesetting industry.</p>
</div>
<div class="abs service-card" style="left:610px">
  <svg width="56" height="56" viewBox="0 0 56 56" fill="none" stroke="#ee1c25" stroke-width="2"><path d="M12 52V10M20 52V10M12 10h40M12 18h40M4 10l8-6 8 6"/><path d="M44 18v12"/><path d="M36 38h16l-4-8h-8z"/><path d="M6 52h20"/></svg>
  <h3 style="top:100px">Construction</h3>
  <p style="top:127px">Lorem Ipsum is simply dummy text of the printing and typesetting industry.</p>
</div>
<div class="abs service-card" style="left:844px">
  <svg width="56" height="56" viewBox="0 0 56 56" fill="none" stroke="#ee1c25" stroke-width="2"><path d="M20 30l16-14 16 14v22H20z"/><path d="M38 28l-6 10h8l-6 10"/><path d="M8 4v10M16 4v10M6 14h12v8H6zM12 22v14c0 8 4 10 8 10"/></svg>
  <h3 style="top:100px">Utility</h3>
  <p style="top:127px">Lorem Ipsum is simply dummy text of the printing and typesetting industry.</p>
</div>

<!-- Vision -->
<div class="abs dots" style="left:141px;top:1048px"><span></span><span></span><span></span><span></span><span></span><span></span><span></span><span></span><span></span><span></span><span></span><span></span><span></span><span></span><span></span></div>
<div class="photo" style="left:183px;top:1066px;width:326px;height:224px;background:linear-gradient(160deg,#8d8f86,#6f7468 50%,#9ea59b)" role="img" aria-label="Aerial view of a boom truck raised over a small town street"></div>
<div class="abs icon-badge" style="left:581px;top:1068px">
  <svg width="28" height="28" viewBox="0 0 28 28" fill="none" stroke="#ee1c25" stroke-width="1.6"><path d="M9 14a5 5 0 1 1 10 0c0 2-2 3-2 6h-6c0-3-2-4-2-6z"/><path d="M11 23h6M12 26h4M14 2v3M4 6l2 2M24 6l-2 2M1 14h3M24 14h3"/></svg>
</div>
<h2 class="abs block-title" style="left:581px;top:1139px">Our Vision</h2>
<div class="abs rule" style="left:581px;top:1184px;width:75px"></div>
<p class="abs block-text" style="left:581px;top:1214px;width:440px">To be the leading provider of aerialaccess, geotechnical drilling, and service solutions, setting the standard forexcellence in safety, efficiency, and environmental stewardship.</p>
<div class="photo" style="left:964px;top:1288px;width:236px;height:92px;background:linear-gradient(180deg,#f4f4f4,#d9d9d9 60%,#f7f7f7)" role="img" aria-label="White boom truck with folded aerial lift"></div>

<!-- Mission -->
<div class="abs icon-badge" style="left:141px;top:1452px">
  <svg width="30" height="30" viewBox="0 0 30 30" fill="none" stroke="#ee1c25" stroke-width="1.6"><circle cx="14" cy="16" r="10"/><circle cx="14" cy="16" r="5.5"/><circle cx="14" cy="16" r="1.5"/><path d="M14 16L25 5M22 4v4h4"/></svg>
</div>
<h2 class="abs block-title" style="left:141px;top:1522px">Our Mission</h2>
<div class="abs rule" style="left:141px;top:1567px;width:76px"></div>
<p class="abs block-text" style="left:141px;top:1597px;width:490px">AtMarlowby, our mission is to deliver unparalleled aerial access, geotechnicaldrilling, and service and maintenance solutions, consistently exceeding ourclients' expectations. We strive to achieve this by investing in cutting-edgetechnology, fostering a culture of safety and continuous improvement, andprioritizing environmental sustainability.</p>
<p class="abs block-text" style="left:141px;top:1724px;width:490px">Through collaboration, integrity, anddedication, we aim to contribute to the success of our clients whilemaintaining the highest standards of quality and professionalism.</p>
<div class="photo" style="left:688px;top:1460px;width:326px;height:370px;background:linear-gradient(180deg,#3f6fc4 0%,#7aa3dc 55%,#c9c9c2 80%,#8e8c82 100%)" role="img" aria-label="Boom truck parked in front of a tall town water tower"></div>
<div class="abs dots" style="left:1025px;top:1441px"><span></span><span></span><span></span><span></span><span></span><span></span><span></span><span></span><span></span><span></span><span></span><span></span><span></span><span></span><span></span></div>

<!-- Divisions -->
<section class="abs divisions"></section>
<h2 class="abs section-title" style="top:1971px">Our Divisions</h2>
<div class="abs rule" style="left:563px;top:2015px;width:74px"></div>

<article class="abs division-card" style="left:141px">
  <div class="photo" style="background:linear-gradient(180deg,#4c7fd0,#a2bde6 60%,#6f6d5e)" role="img" aria-label="Aerial lift working beside a tall water tower"></div>
  <h3>Aerial Access</h3>
  <p>Marlowby is a full-service wind energy service provider specializing in blade access &amp; repair, service and maintenance &amp; trouble shooting on most wind turbine platforms.</p>
</article>
<article class="abs division-card active" style="left:454px">
  <div class="photo" style="background:linear-gradient(160deg,#2d4a22,#4f7a35 50%,#27401c)" role="img" aria-label="Red tracked geotechnical drilling rig on a green hillside"></div>
  <h3>Geotechnical Drilling</h3>
  <p>There are many variations of passages of Lorem Ipsum available, but the majority have suffered alteration in some form, by injected humour, or randomised words.</p>
  <div class="read-more"><span>Read More</span><svg width="16" height="10" viewBox="0 0 16 10" fill="none" stroke="#fff" stroke-width="1.4"><path d="M0 5h14M10 1l4 4-4 4"/></svg></div>
</article>
<article class="abs division-card" style="left:767px">
  <div class="photo" style="background:linear-gradient(160deg,#1f5fcf,#4a86e0 60%,#7eaaea)" role="img" aria-label="Wind turbine against a clear blue sky"></div>
  <h3>Renewable Energy Services</h3>
  <p>There are many variations of passages of Lorem Ipsum available, but the majority have suffered alteration in some form, by injected humour, or randomised words.</p>
</article>

<!-- Closing -->
<p class="abs closing-text">Marlowby Is A Full-Service Wind Energy Service Provider Specializing In Blade Access And Repair, Service And Maintenance, And Trouble Shooting On Most Wind Turbine Platforms.</p>
<div class="photo" style="left:431px;top:2651px;width:338px;height:133px;background:linear-gradient(180deg,#f6f6f6,#dedede 55%,#f8f8f8)" role="img" aria-label="White boom truck with folded aerial lift"></div>
<div class="abs btn closing-cta">Contact Us</div>

<!-- Footer -->
<footer class="abs footer">
  <div class="abs logo">MARLOWBY</div>
  <div class="abs" style="left:450px;top:56px">
    <h4>Quick Links</h4>
    <ul style="margin-top:10px"><li>Home</li><li>About Us</li><li>Services</li><li>Safety</li><li>Careers</li></ul>
  </div>
  <div class="abs" style="left:651px;top:56px">
    <h4>Company</h4>
    <ul style="margin-top:10px"><li>Terms &amp; Condition</li><li>Privacy Policy</li><li>Contact Us</li></ul>
  </div>
  <div class="abs" style="left:849px;top:56px;width:215px">
    <h4>Contact Info</h4>
    <div class="contact-item" style="margin-top:16px">
      <svg width="18" height="18" viewBox="0 0 18 18" fill="none" stroke="#ee1c25" stroke-width="1.6"><path d="M9 17s-5-5-5-9a5 5 0 0 1 10 0c0 4-5 9-5 9z"/><circle cx="9" cy="8" r="1.8"/></svg>
      <span>218 Harrow Lane Eastvale<br>AB T9X-4K1</span>
    </div>
    <div class="contact-item" style="margin-top:10px">
      <svg width="18" height="14" viewBox="0 0 18 14"><rect x="1" y="1" width="16" height="12" fill="#ee1c25"/><path d="M1 2l8 6 8-6" fill="none" stroke="#fff" stroke-width="1.3"/></svg>
      <span>info@marlowby.example</span>
    </div>
    <div class="contact-item" style="margin-top:10px">
      <svg width="16" height="16" viewBox="0 0 16 16"><path d="M3 1l3 3-2 2c1 2 3 4 5 5l2-2 3 3-2 3C7 14 2 9 1 3z" fill="#ee1c25"/></svg>
      <span>555 014 2290</span>
    </div>
  </div>
  <div class="abs footer-rule"></div>
  <p class="abs copyright">© 2024 Marlowby. All Rights Reserved.</p>
  <div class="abs socials" aria-label="Social links"><span></span><span></span><span></span><span></span></div>
</footer>

</body>
</html>
```